Clear Harbor Business card

We are a company that owns 2 compliance software programs for TV, Radio and Cable industries as well as an online job board. We need a professional business card that incorproates all three logos.

```html
<!DOCTYPE html>
<html lang="en">
<head>
<meta charset="utf-8">
<title>Clear Harbor Business Card</title>
<link href="https://fonts.googleapis.com/css2?family=Roboto:wght@400;500;700&display=swap" rel="stylesheet">
<style>
  :root {
    --stage: #e6e6e8;
    --red: #e8341f;
    --navy: #1b1a5e;
    --paper: #ffffff;
    --ink: #3a3a3a;
    --rule: #9a9a9a;
    --sky: #2f8fd8;
  }
  * { margin: 0; padding: 0; box-sizing: border-box; }
  html, body { width: 1200px; height: 874px; overflow: hidden; }
  body {
    background: var(--stage);
    font-family: "Roboto", Arial, sans-serif;
    position: relative;
  }
  .card {
    position: absolute;
    left: 280px;
    width: 640px;
    height: 366px;
    overflow: hidden;
    box-shadow: 0 6px 18px rgba(0,0,0,.18);
  }
  .card-front { top: 40px; background: var(--red); color: var(--paper); }
  .card-back { top: 452px; background: var(--paper); }

  .brand-row {
    position: absolute;
    left: 0; right: 0;
    display: flex;
    justify-content: center;
    align-items: center;
    gap: 22px;
  }
  .card-front .brand-row { top: 128px; }
  .card-back .brand-row { top: 50px; }
  .brand {
    display: flex;
    flex-direction: column;
    align-items: flex-start;
    font-weight: 700;
    font-size: 22px;
    line-height: 1;
  }
  .brand-tag {
    font-size: 7px;
    font-weight: 700;
    letter-spacing: .6px;
    text-transform: uppercase;
    margin-top: 4px;
  }
  .brand-mark {
    display: flex;
    align-items: center;
    gap: 7px;
  }
  .brand-dot {
    width: 22px; height: 22px;
    border-radius: 50%;
    background: var(--sky);
  }
  .divider { width: 1.5px; height: 62px; }
  .card-front .divider { background: var(--paper); }
  .card-back .divider { background: var(--navy); }
  .card-front .brand { color: var(--paper); }
  .card-back .brand { color: var(--navy); }
  .card-back .brand-mark .brand { color: var(--sky); }

  .website {
    position: absolute;
    left: 0; right: 0; top: 290px;
    text-align: center;
    font-size: 14px;
    letter-spacing: 7px;
  }

  .holder {
    position: absolute;
    left: 60px; top: 180px;
    width: 250px;
    text-align: right;
  }
  .holder-name { color: var(--navy); font-weight: 700; font-size: 24px; }
  .holder-role { color: var(--red); font-weight: 500; font-size: 15px; margin-top: 3px; }
  .holder-address { color: var(--ink); font-size: 14px; line-height: 1.45; margin-top: 8px; }

  .contact-rule {
    position: absolute;
    left: 330px; top: 188px;
    width: 1.5px; height: 100px;
    background: linear-gradient(var(--paper), var(--rule), var(--paper));
  }
  .contact {
    position: absolute;
    left: 350px; top: 196px;
    list-style: none;
    color: var(--ink);
    font-size: 15px;
  }
  .contact li { display: flex; align-items: center; gap: 9px; height: 22px; }
  .contact svg { width: 14px; height: 14px; fill: var(--navy); }

  .band { position: absolute; bottom: 0; height: 16px; }
  .band-navy { left: 0; width: 62%; background: var(--navy); }
  .band-red { left: 62%; right: 0; background: var(--red); }
</style>
</head>
<body>

<section class="card card-front">
  <div class="brand-row">
    <div class="brand">Clear Harbor<span class="brand-tag">Broadcast Compliance</span></div>
    <div class="divider"></div>
    <div class="brand">Cable Harbor<span class="brand-tag">MVPD Compliance</span></div>
    <div class="divider"></div>
    <div class="brand-mark"><span class="brand-dot"></span><span class="brand">CrewBoard.co</span></div>
  </div>
  <p class="website">www.clearharbor.co</p>
</section>

<section class="card card-back">
  <div class="brand-row">
    <div class="brand">Clear Harbor<span class="brand-tag">Broadcast Compliance</span></div>
    <div class="divider"></div>
    <div class="brand">Cable Harbor<span class="brand-tag">MVPD Compliance</span></div>
    <div class="divider"></div>
    <div class="brand-mark"><span class="brand-dot"></span><span class="brand">CrewBoard.co</span></div>
  </div>

  <div class="holder">
    <p class="holder-name">DANA REYES</p>
    <p class="holder-role">CEO/FOUNDER</p>
    <p class="holder-address">412 Linden Court<br>Juneau, Alaska 99801</p>
  </div>

  <div class="contact-rule"></div>

  <ul class="contact">
    <li><svg viewBox="0 0 24 24"><path d="M6.6 10.8a15 15 0 0 0 6.6 6.6l2.2-2.2a1 1 0 0 1 1-.25 11.4 11.4 0 0 0 3.6.57 1 1 0 0 1 1 1V20a1 1 0 0 1-1 1A17 17 0 0 1 3 4a1 1 0 0 1 1-1h3.5a1 1 0 0 1 1 1c0 1.25.2 2.45.57 3.57a1 1 0 0 1-.25 1z"/></svg>555 014 2291</li>
    <li><svg viewBox="0 0 24 24"><path d="M7 1h10a2 2 0 0 1 2 2v18a2 2 0 0 1-2 2H7a2 2 0 0 1-2-2V3a2 2 0 0 1 2-2zm0 3v14h10V4z"/></svg>555 017 6640</li>
    <li><svg viewBox="0 0 24 24"><path d="M6 2h12v5H6zM3 8h18a2 2 0 0 1 2 2v7h-4v5H5v-5H1v-7a2 2 0 0 1 2-2zm4 8v4h10v-4z"/></svg>555 019 3382</li>
    <li><svg viewBox="0 0 24 24"><path d="M2 5h20v14H2zm2 2v.5l8 5 8-5V7l-8 5z"/></svg>dana@clearharbor.co</li>
  </ul>

  <div class="band band-navy"></div>
  <div class="band band-red"></div>
</section>

</body>
</html>
```